Vernac Law Business cards and stationary design project

We are looking for a stationary design for business cards (double sided), 8x10, 5x7, and legal and standard envelopes.

We would like the design to match the logo that we have already.
Color palate preferred is Teal, White, grey and any others that will look good for a professional law firm.

We would like this statement: "RELATIONSHIPS. RESPECT. RESULT" to be on the back of the business cards and maybe on the stationary if it looks good.

Please see link to website for more information: www.vernac-law.example

Target Market(s)

Potential clients that need Attorney services.

Industry/Entity Type

Law Firm

Contact Information for Business Card

We would like the front and back to be two different colors. Current business cards are teal front, grey back and are a vertical design. We are open to options with colors.

Font styles to use
Serif

Colors
33a6d7
33b8a4
b9b9b9
5c5c5c

Requirements
Must have
• Logo supplied needs to go on the card and stationary.
• Match website color palate, www.vernac-law.example
• Be professional and not too wordy.
• Criminal Law, Civil Litigation, Personal Injury, Restraining Orders need to be on the card.
Nice to have
• RELATIONSHIPS. RESPECT. RESULTS. on the back of the card.
Should not have
• Not be too busy/wordy or too flashy.

```html
<!DOCTYPE html>
<html lang="en">
<head>
<meta charset="utf-8">
<title>Vernac Law — Business Card</title>
<link rel="stylesheet" href="https://fonts.googleapis.com/css2?family=Open+Sans:wght@400;600;700&display=swap">
<style>
  :root {
    --teal: #12899a;
    --ink: #111111;
    --paper: #ffffff;
    --backdrop: #e9e9e7;
    --shadow: rgba(0, 0, 0, 0.12);
  }
  * { box-sizing: border-box; margin: 0; padding: 0; }
  html, body {
    width: 1200px; height: 900px; overflow: hidden;
    background: var(--backdrop);
    font-family: "Open Sans", Arial, sans-serif;
  }
  .canvas { position: relative; width: 1200px; height: 900px; }

  .card {
    position: absolute;
    background: var(--paper);
    box-shadow: 0 6px 18px var(--shadow);
    overflow: hidden;
  }
  .card-front { left: 65px; top: 42px; width: 607px; height: 370px; }
  .card-back  { left: 388px; top: 505px; width: 567px; height: 352px; }

  .card-swoosh { position: absolute; inset: 0; width: 100%; height: 100%; }

  .contact-name {
    position: absolute; left: 0; right: 0; top: 37px;
    text-align: center; color: var(--teal);
    font-weight: 700; font-size: 20px; letter-spacing: 0.2px;
  }
  .contact-title {
    position: absolute; left: 0; right: 0; top: 63px;
    text-align: center; color: var(--ink); font-size: 15px;
  }

  .firm-name {
    position: absolute; left: 0; right: 0;
    display: flex; align-items: center; justify-content: center; gap: 14px;
    color: var(--teal); font-weight: 600; letter-spacing: 3px;
    text-transform: uppercase;
  }
  .firm-name .mark { width: 14px; height: 14px; background: var(--teal); }
  .card-front .firm-name { top: 118px; font-size: 38px; }
  .card-back  .firm-name { top: 105px; font-size: 36px; }

  .contact-lines {
    position: absolute; left: 0; right: 0; top: 216px;
    text-align: center; color: var(--ink); font-size: 15px; line-height: 25px;
  }
  .contact-lines .icon { width: 12px; height: 10px; vertical-align: 0; margin-right: 3px; fill: var(--teal); }

  .address {
    position: absolute; left: 121px; top: 330px;
    color: var(--paper); font-size: 15px;
  }
  .tagline {
    position: absolute; left: 0; right: 0; top: 313px;
    text-align: center; color: var(--paper);
    font-weight: 600; font-size: 15.5px; letter-spacing: 0.2px;
  }
</style>
</head>
<body>
<main class="canvas">

  <section class="card card-front" aria-label="Business card front">
    <svg class="card-swoosh" viewBox="0 0 607 370" preserveAspectRatio="none" aria-hidden="true">
      <path d="M105 306 C250 284 420 280 607 300 L607 332 C470 300 300 296 105 306 Z" fill="var(--ink)"/>
      <path d="M0 336 C150 300 420 292 607 320 L607 370 L0 370 Z" fill="var(--teal)"/>
    </svg>
    <div class="contact-name">JOHN SMITH</div>
    <div class="contact-title">Managing Direcator</div>
    <div class="firm-name"><span class="mark"></span>Vernac Law</div>
    <div class="contact-lines">
      <div><svg class="icon" viewBox="0 0 12 10"><path d="M1 3 C1 1 3 0 6 0 C9 0 11 1 11 3 L9 4 L8 2.5 L4 2.5 L3 4 Z M2 5 L10 5 L11 10 L1 10 Z"/></svg>823-456-7890</div>
      <div><svg class="icon" viewBox="0 0 12 10"><path d="M0 0 L12 0 L6 5 Z M0 1.5 L6 6.5 L12 1.5 L12 10 L0 10 Z"/></svg>info@youremail.com</div>
    </div>
    <div class="address">1234, Address Goes Here Country Name, 123456</div>
  </section>

  <section class="card card-back" aria-label="Business card back">
    <svg class="card-swoosh" viewBox="0 0 567 352" preserveAspectRatio="none" aria-hidden="true">
      <path d="M0 285 C160 262 330 262 470 290 C320 276 160 282 0 310 Z" fill="var(--ink)"/>
      <path d="M0 310 C180 280 400 278 567 312 L567 352 L0 352 Z" fill="var(--teal)"/>
    </svg>
    <div class="firm-name"><span class="mark"></span>Vernac Law</div>
    <div class="tagline">RELATIONSHIPS. RESPECT. RESULT</div>
  </section>

</main>
</body>
</html>
```